Lorna Vale Industries Wix Site

Company website run as a hobby by my daughter Lorna. She wants to be able to offer multiple products for sale online (so etail enabled). Personalized products like bracelets and necklaces with people's names. Piggy Banks with kids names. Trail Keeper cookies when in season. Not childish in presentation but easy to navigate by kids. Big images like on original website (lornavalebakes.com). Same humor as on that site (go to the cart and empty it and you will get the idea. Colors Gold like on the bird in her attached card. Blue should be lighter than that card (robins egg type of blue). Avoid the green on the biz card. Basics of a new website with About Us, Contact, social media and a cart with payment options via coinrill. mobile version nice to have but not mandataory.

```html
<!DOCTYPE html>
<html lang="en">
<head>
<meta charset="utf-8">
<title>Lorna Biz</title>
<link href="https://fonts.googleapis.com/css2?family=Oswald:wght@200;300;400&display=swap" rel="stylesheet">
<style>
:root{
  --sky:#dff6f8;
  --robin:#bae4e9;
  --gold:#b8933a;
  --gold-dark:#5e4814;
  --ink:#2b2b2b;
  --white:#ffffff;
  --accent:#3fb7cf;
}
*{box-sizing:border-box;margin:0;padding:0}
html,body{width:720px;height:1200px;overflow:hidden}
body{font-family:"Oswald",sans-serif;font-weight:300;color:var(--ink);background:var(--robin)}
.page{position:relative;width:720px;height:1200px;overflow:hidden;background:var(--robin)}
.sky-band{position:absolute;left:0;top:0;width:720px;height:356px;background:var(--sky)}
.brand{position:absolute;left:0;top:14px;width:720px;height:84px}
.brand-mark{position:absolute;left:346px;top:4px;width:28px;height:28px;border-radius:50%;background:var(--gold)}
.brand-name{position:absolute;left:0;top:48px;width:720px;height:30px;line-height:30px;text-align:center;color:var(--gold-dark);font-size:20px;font-weight:300;letter-spacing:0}
.main-nav{position:absolute;left:102px;top:103px;width:515px;height:45px;background:var(--gold)}
.main-nav a{position:absolute;top:0;line-height:45px;color:var(--white);font-size:12.5px;text-decoration:none;letter-spacing:.2px}
.cart-button{position:absolute;left:417px;top:11px;width:89px;height:26px;background:var(--gold-dark);border:1px solid #3e2f0a;color:var(--white);font-size:8.5px;line-height:24px;text-align:center;letter-spacing:-.2px}
.cart-button svg{vertical-align:-2px;margin-right:3px}
.hero{position:absolute;left:102px;top:148px;width:515px;height:318px;background:linear-gradient(120deg,#f7f7f4,#efefeb 60%,#ecece7)}
.hero-card{position:absolute;left:264px;top:104px;width:204px;height:129px;background:var(--gold);text-align:center}
.hero-kicker{position:absolute;left:0;top:14px;width:100%;font-size:25px;line-height:30px;font-weight:300;color:#111;letter-spacing:1px}
.hero-title{position:absolute;left:0;top:40px;width:100%;font-size:40px;line-height:42px;font-weight:300;color:var(--white);letter-spacing:1.5px}
.hero-button{position:absolute;left:58px;top:86px;width:88px;height:24px;background:var(--gold-dark);color:var(--white);font-size:8.5px;line-height:24px}
.hero-dots{position:absolute;left:333px;top:443px}
.hero-dots span{position:absolute;top:0;width:8px;height:8px;background:#c9a85a}
.hero-dots span.active{background:var(--gold-dark)}
.section-title{position:absolute;left:0;top:490px;width:720px;text-align:center;font-size:15px;font-weight:300;letter-spacing:.5px;color:#1d1d1d}
.product{position:absolute;width:152px;height:206px;background:var(--white)}
.product-photo{position:absolute;left:0;top:0;width:152px;height:116px;background:radial-gradient(circle at 50% 45%,#e9e9ee,#ffffff 70%)}
.product-photo.pink{background:radial-gradient(circle at 50% 45%,#eba2aa,#ffffff 62%)}
.product-name{position:absolute;left:0;top:126px;width:100%;text-align:center;font-size:10px;letter-spacing:2px;color:#555;font-weight:300}
.product-price{position:absolute;left:0;top:140px;width:100%;text-align:center;font-size:17px;color:#333;font-weight:300}
.add-to-cart{position:absolute;left:0;bottom:0;width:152px;height:33px;background:var(--gold);color:#f3ead4;font-size:10px;line-height:33px;text-align:center;letter-spacing:.5px}
.add-to-cart svg{vertical-align:-2px;margin-right:5px}
.carousel-arrow{position:absolute;top:757px}
.contact-strip{position:absolute;left:0;top:990px;width:720px;height:88px}
.contact-item{position:absolute;top:0;width:180px;text-align:center;color:#2f2f2f}
.contact-item svg{display:block;margin:6px auto 0}
.contact-label{font-size:11px;margin-top:8px}
.contact-value{font-size:13px;margin-top:1px;letter-spacing:.3px}
.divider{position:absolute;top:0;width:1px;height:86px;background:#e9f6f8}
.site-footer{position:absolute;left:0;top:1098px;width:720px;height:102px;background:var(--sky)}
.social{position:absolute;left:0;top:18px;width:720px;text-align:center;font-size:9.5px;color:#2f2f2f}
.social span{display:inline-block;margin:0 9px;line-height:22px}
.social i{display:inline-block;width:9px;height:9px;border-radius:50%;margin-right:5px;vertical-align:-1px}
.footer-nav{position:absolute;left:0;top:52px;width:720px;text-align:center;font-size:9px;color:#222}
.footer-nav a{color:#222;text-decoration:none;margin:0 9px}
.copyright{position:absolute;left:0;top:73px;width:720px;text-align:center;font-size:8.5px;color:#222}
</style>
</head>
<body>
<div class="page">
  <div class="sky-band"></div>

  <header class="brand">
    <div class="brand-mark"></div>
    <div class="brand-name">LORNA BIZ</div>
  </header>

  <nav class="main-nav">
    <a style="left:18px">HOME</a>
    <a style="left:62px">ABOUT US</a>
    <a style="left:127px">PRODUCTS</a>
    <a style="left:196px">STORES</a>
    <a style="left:249px">SALES</a>
    <a style="left:294px">CONTACT US</a>
    <div class="cart-button">
      <svg width="11" height="10" viewBox="0 0 11 10"><path d="M0 1h2l2 6h6l1-4H3" fill="none" stroke="#fff" stroke-width="1"/><circle cx="5" cy="9" r="1" fill="#fff"/><circle cx="9" cy="9" r="1" fill="#fff"/></svg>MY CART : 0 ITEMS
    </div>
  </nav>

  <section class="hero" role="img" aria-label="Silver pendant necklace engraved with a name, on a light background">
    <div class="hero-card">
      <div class="hero-kicker">NECKLACE WITH</div>
      <div class="hero-title">NECKLACE</div>
      <div class="hero-button">VIEW COLLECTIONS</div>
    </div>
  </section>
  <div class="hero-dots">
    <span class="active" style="left:0"></span><span style="left:15px"></span><span style="left:30px"></span><span style="left:45px"></span>
  </div>

  <h2 class="section-title">OUR PRODUCTS</h2>

  <svg class="carousel-arrow" style="left:93px" width="10" height="16" viewBox="0 0 10 16" aria-hidden="true"><path d="M8 2 2 8l6 6" fill="none" stroke="#fff" stroke-width="2.5"/></svg>
  <svg class="carousel-arrow" style="left:617px" width="10" height="16" viewBox="0 0 10 16" aria-hidden="true"><path d="M2 2l6 6-6 6" fill="none" stroke="#fff" stroke-width="2.5"/></svg>

  <article class="product" style="left:118px;top:524px">
    <div class="product-photo" role="img" aria-label="Layered silver chain necklaces with script name pendant"></div>
    <div class="product-name">NECKLACE NAME</div><div class="product-price">$10.00</div>
    <div class="add-to-cart"><svg width="12" height="10" viewBox="0 0 11 10"><path d="M0 1h2l2 6h6l1-4H3" fill="none" stroke="#f3ead4"/><circle cx="5" cy="9" r="1" fill="#f3ead4"/><circle cx="9" cy="9" r="1" fill="#f3ead4"/></svg>ADD TO CART</div>
  </article>
  <article class="product" style="left:284px;top:524px">
    <div class="product-photo" role="img" aria-label="Silver script name necklace"></div>
    <div class="product-name">NECKLACE NAME</div><div class="product-price">$10.00</div>
    <div class="add-to-cart"><svg width="12" height="10" viewBox="0 0 11 10"><path d="M0 1h2l2 6h6l1-4H3" fill="none" stroke="#f3ead4"/><circle cx="5" cy="9" r="1" fill="#f3ead4"/><circle cx="9" cy="9" r="1" fill="#f3ead4"/></svg>ADD TO CART</div>
  </article>
  <article class="product" style="left:450px;top:524px">
    <div class="product-photo pink" role="img" aria-label="Pink piggy bank with a name label"></div>
    <div class="product-name">NECKLACE NAME</div><div class="product-price">$10.00</div>
    <div class="add-to-cart"><svg width="12" height="10" viewBox="0 0 11 10"><path d="M0 1h2l2 6h6l1-4H3" fill="none" stroke="#f3ead4"/><circle cx="5" cy="9" r="1" fill="#f3ead4"/><circle cx="9" cy="9" r="1" fill="#f3ead4"/></svg>ADD TO CART</div>
  </article>
  <article class="product" style="left:118px;top:749px">
    <div class="product-photo" role="img" aria-label="Silver script word necklace"></div>
    <div class="product-name">BRACELET NAME</div><div class="product-price">$10.00</div>
    <div class="add-to-cart"><svg width="12" height="10" viewBox="0 0 11 10"><path d="M0 1h2l2 6h6l1-4H3" fill="none" stroke="#f3ead4"/><circle cx="5" cy="9" r="1" fill="#f3ead4"/><circle cx="9" cy="9" r="1" fill="#f3ead4"/></svg>ADD TO CART</div>
  </article>
  <article class="product" style="left:284px;top:749px">
    <div class="product-photo" role="img" aria-label="Chain bracelet with engraved name plate"></div>
    <div class="product-name">PIGGY BANK NAME</div><div class="product-price">$10.00</div>
    <div class="add-to-cart"><svg width="12" height="10" viewBox="0 0 11 10"><path d="M0 1h2l2 6h6l1-4H3" fill="none" stroke="#f3ead4"/><circle cx="5" cy="9" r="1" fill="#f3ead4"/><circle cx="9" cy="9" r="1" fill="#f3ead4"/></svg>ADD TO CART</div>
  </article>
  <article class="product" style="left:450px;top:749px">
    <div class="product-photo" role="img" aria-label="Silver letter bead bracelet"></div>
    <div class="product-name">NECKLACE NAME</div><div class="product-price">$10.00</div>
    <div class="add-to-cart"><svg width="12" height="10" viewBox="0 0 11 10"><path d="M0 1h2l2 6h6l1-4H3" fill="none" stroke="#f3ead4"/><circle cx="5" cy="9" r="1" fill="#f3ead4"/><circle cx="9" cy="9" r="1" fill="#f3ead4"/></svg>ADD TO CART</div>
  </article>

  <section class="contact-strip">
    <div class="contact-item" style="left:93px">
      <svg width="22" height="22" viewBox="0 0 22 22" aria-hidden="true"><circle cx="11" cy="11" r="10" fill="var(--accent)"/></svg>
      <div class="contact-label">FOLLOW ME ON CHIRPLINE</div>
      <div class="contact-value">@LORNA BIZ</div>
    </div>
    <div class="divider" style="left:278px"></div>
    <div class="contact-item" style="left:269px">
      <svg width="34" height="28" viewBox="0 0 34 28" aria-hidden="true"><path d="M5 16a12 12 0 0 1 24 0" fill="none" stroke="var(--accent)" stroke-width="3"/><rect x="3" y="14" width="6" height="10" rx="2" fill="var(--accent)"/><rect x="25" y="14" width="6" height="10" rx="2" fill="var(--accent)"/><circle cx="17" cy="16" r="6" fill="var(--accent)"/><path d="M28 23q-3 4-9 4" fill="none" stroke="var(--accent)" stroke-width="2"/></svg>
      <div class="contact-label">CALL ME ORDER NOW</div>
      <div class="contact-value">1-555-014-2273</div>
    </div>
    <div class="divider" style="left:449px"></div>
    <div class="contact-item" style="left:448px">
      <svg width="28" height="22" viewBox="0 0 28 22" aria-hidden="true"><rect x="1" y="3" width="26" height="17" fill="var(--accent)"/><path d="M1 3l13 10L27 3" fill="none" stroke="#e6f7fa" stroke-width="1.5"/></svg>
      <div class="contact-label">SAY HELLO BY EMAIL</div>
      <div class="contact-value">LORNABIZ@MAILDRIFT.COM</div>
    </div>
  </section>

  <footer class="site-footer">
    <div class="social">
      <span><i style="background:var(--accent)"></i>Chirpline</span>
      <span><i style="background:#3b5ea8"></i>Friendwall</span>
      <span><i style="background:#1a88b8"></i>Workmesh</span>
    </div>
    <nav class="footer-nav">
      <a>HOME</a>I<a>ABOUT US</a>I<a>PRODUCTS</a>I<a>STORES</a>I<a>SALES</a>I<a>CONTACT US</a>
    </nav>
    <div class="copyright">©2014 COMPANY NAME,ALL RIGHTS RESERVED</div>
  </footer>
</div>
</body>
</html>
```